Sprout & Shine General Card Design

Please see http://sprout-and-shine.example.org for more information about our program. In brief, we are a 501(c)(3) nonprofit organization that focuses on improving educational outcomes for all students through parent education and empowerment, K-12 curriculum development, K-12 staff development, learner-oriented live events, community service projects, and more. We are now preparing to launch our Sprout & Shine Educational Series, which is devoted to teaching children and the adults in their lives about making healthy food choices and regaining control over what is in their food by growing it themselves in easy, affordable self-watering container gardens that can be placed in spaces not otherwise suitable for growing fruits and vegetables, such as paved lots and rooftops, are portable, and can be quickly built from recycled materials. In fact, we have local businesses already lining up to donate clean, safe 5-gallon buckets for this initiative (our container design uses 5-gallon buckets). We have already built out content on the site to support as many of the Trail Ranger merit badges as we could tie to the instructional goals of our Sprout & Shine Educational Series. We are in the processes of developing K-12 curricula tied to the Common Core and STEM (science, technology, engineering, & math), which we will be giving away for free under a Creative Commons license to help public schools in states that have recently adopted the Common Core but can't afford to replace all their textbooks and don't have the time to scramble to create curricula of their own. This card will be used by all of our Sprout & Shine staff and volunteers to share out information about the program and promote it to others. It will go out in mailings, sit on display tables at events, be left at kiosks, and be handed out in person. It needs to be color-matched to our Sprout & Shine site. The logo on the site we created for our Sprout & Shine Educational Series was done using an online service and the quality of the image is quite poor (see attached file). When we use it in print materials and then convert them to PDF, the logo becomes pixelated. It's awful. We are not entirely married to keeping the logo if you can come up with something better and we are given the final JPG or PNG file of the logo to upload to the site so they match. If you can just improve the quality of the existing logo, that's fine, too. Please note that the phrase "Sprout & Shine Educational Series" is a service mark of Tamarind Valley Families and should be followed by the letters "SM" in superscript at the end of the word "Series" in any logo you create.
Target Market(s)
parents of K-12 students, K-12 teachers, community service organizations, youth organizations, programs for the elderly, programs for the disabled
Industry/Entity Type
Community Service
Contact Information for Business Card
TMV4Families' Sprout & Shine Educational Series, http://sprout-and-shine.example.org, (555) 214-7390, Non-GMO/Organic Family & Community Gardening Workshops, K-12 Common Core/STEM Curricula Development, Community Service Projects, Online Gardening & Teaching Communities, Project-Based Learning Activities, Youth Leadership Projects, Fun Contests and Prizes, Corporate & Small Business Social Responsibility Programs, K-12 Staff Development, Education Research & Reporting

```html
<!DOCTYPE html>
<html lang="en">
<head>
<meta charset="utf-8">
<title>Sprout &amp; Shine Educational Series – Card Options</title>
<link rel="stylesheet" href="https://fonts.googleapis.com/css2?family=Crete+Round&family=Questrial&family=Arimo:wght@400;700&display=swap">
<style>
  :root {
    --paper: #ffffff;
    --label: #333333;
    --ink-green: #3d6b1a;
    --accent-orange: #f5921e;
    --accent-yellow: #f7d23a;
    --sage: #b3cc97;
    --sage-bar: #5b8a2d;
    --sage-ink: #4d8024;
    --sage-text: #3b4a30;
    --arc-green: #8fbd3f;
    --brand-ink: #1f4d0c;
  }
  * { margin: 0; padding: 0; box-sizing: border-box; }
  html, body { width: 727px; height: 1200px; overflow: hidden; background: var(--paper); }
  .sheet { position: relative; width: 727px; height: 1200px; }
  .option-label { position: absolute; font: 400 38px Arimo, Arial, sans-serif; color: var(--label); }
  .card { position: absolute; overflow: hidden; box-shadow: 3px 4px 8px rgba(0,0,0,.28); }
  .card svg.art { position: absolute; inset: 0; }
  .abs { position: absolute; }
  sup { font-size: .42em; vertical-align: super; }

  /* Option 1 – vertical cards */
  .v-card { width: 267px; height: 460px; }
  .v-title { font-family: "Crete Round", Georgia, serif; color: var(--ink-green); text-align: center; width: 100%; line-height: 1; }
  .v-title .name { display: block; font-size: 30px; }
  .v-title .series { display: block; font-size: 22px; margin-top: 5px; }
  .v-contact { width: 100%; text-align: center; font: 700 14px Arimo, Arial, sans-serif; color: var(--brand-ink); }
  .v-contact p { margin-bottom: 10px; }
  .v-contact svg { vertical-align: -3px; margin-right: 3px; }
  .brand-name { font: 700 16px Arimo, Arial, sans-serif; color: var(--brand-ink); white-space: nowrap; }
  .v-list { list-style: none; left: 22px; right: 12px; font: 400 11.5px/16px Arimo, Arial, sans-serif; color: #2c4418; }
  .v-list li { position: relative; padding-left: 14px; }
  .v-list li::before { content: ""; position: absolute; left: 0; top: 5px; width: 6px; height: 6px; border-radius: 50%; background: var(--accent-orange); }

  /* Option 2 – horizontal cards */
  .h-card { width: 454px; height: 276px; background: var(--sage); }
  .h-bar { position: absolute; left: 0; top: 0; width: 100%; height: 15px; background: var(--sage-bar); }
  .h-title { font-family: Questrial, "Century Gothic", sans-serif; color: var(--sage-ink); line-height: 1; }
  .h-contact { font: 700 14px Arimo, Arial, sans-serif; color: #2f5a14; }
  .h-contact p { display: flex; align-items: center; gap: 10px; margin-bottom: 14px; }
  .h-list { list-style: none; font: 400 11.5px/16.6px Arimo, Arial, sans-serif; color: var(--sage-text); }
  .h-list li { position: relative; padding-left: 10px; }
  .h-list li::before { content: ""; position: absolute; left: 0; top: 7px; width: 4px; height: 4px; border-radius: 50%; background: var(--sage-ink); }
</style>
</head>
<body>
<main class="sheet">

  <span class="option-label" style="left:24px;top:46px;">1</span>

  <!-- Option 1 front -->
  <section class="card v-card" style="left:71px;top:45px;">
    <svg class="art" width="267" height="460" viewBox="0 0 267 460">
      <defs>
        <linearGradient id="vGreen" x1="0" y1="0" x2="0" y2="1">
          <stop offset="0" stop-color="#e6f2c8"/>
          <stop offset=".45" stop-color="#a9d35a"/>
          <stop offset="1" stop-color="#5e9c2a"/>
        </linearGradient>
        <linearGradient id="vFoliage" x1="0" y1="0" x2="1" y2="1">
          <stop offset="0" stop-color="#9cbf6e"/>
          <stop offset="1" stop-color="#3f6a22"/>
        </linearGradient>
        <linearGradient id="vMeadow" x1="0" y1="0" x2="0" y2="1">
          <stop offset="0" stop-color="#7d9a4c"/>
          <stop offset="1" stop-color="#3e5e24"/>
        </linearGradient>
      </defs>
      <rect width="267" height="460" fill="url(#vGreen)"/>
      <path d="M0 135 Q120 110 267 92" stroke="var(--accent-yellow)" stroke-width="8" fill="none"/>
      <path d="M0 128 Q120 104 267 86" stroke="var(--accent-orange)" stroke-width="6" fill="none"/>
      <path d="M0 0 H267 V86 Q120 104 0 126 Z" fill="url(#vFoliage)" role="img" aria-label="Photo: green bean pods hanging among leaves"/>
      <path d="M0 318 Q140 280 267 290" stroke="var(--accent-orange)" stroke-width="6" fill="none"/>
      <path d="M0 324 Q140 286 267 296 V460 H0 Z" fill="url(#vMeadow)" role="img" aria-label="Photo: children exploring a meadow with a field guide"/>
    </svg>
    <h1 class="v-title abs" style="top:160px;">
      <span class="name">Sprout &amp; Shine</span>
      <span class="series">Educational Series<sup>SM</sup></span>
    </h1>
    <div class="v-contact abs" style="top:238px;">
      <p>www.sprout-and-shine.example.org</p>
      <p><svg width="14" height="14" viewBox="0 0 24 24"><path d="M6.6 10.8a15.1 15.1 0 0 0 6.6 6.6l2.2-2.2c.3-.3.7-.4 1-.2 1.1.4 2.3.6 3.6.6.6 0 1 .4 1 1V20c0 .6-.4 1-1 1A17 17 0 0 1 3 4c0-.6.4-1 1-1h3.5c.6 0 1 .4 1 1 0 1.3.2 2.5.6 3.6.1.3 0 .7-.2 1z" fill="#1f4d0c"/></svg>(555) 214-7390</p>
    </div>
    <span class="brand-name abs" style="left:12px;top:430px;">Tamarind Valley Families</span>
  </section>

  <!-- Option 1 back -->
  <section class="card v-card" style="left:401px;top:45px;">
    <svg class="art" width="267" height="460" viewBox="0 0 267 460">
      <defs>
        <linearGradient id="vGreenB" x1="0" y1="0" x2="1" y2="1">
          <stop offset="0" stop-color="#8dc63f"/>
          <stop offset=".5" stop-color="#eef6dc"/>
          <stop offset="1" stop-color="#8dc63f"/>
        </linearGradient>
        <linearGradient id="vEgg" x1="0" y1="0" x2="1" y2="0">
          <stop offset="0" stop-color="#9fb07a"/>
          <stop offset=".5" stop-color="#dedbd0"/>
          <stop offset="1" stop-color="#b9c0a6"/>
        </linearGradient>
      </defs>
      <rect width="267" height="460" fill="url(#vGreenB)"/>
      <path d="M0 356 Q120 300 267 352" stroke="var(--accent-orange)" stroke-width="6" fill="none"/>
      <path d="M0 362 Q120 306 267 358 V460 H0 Z" fill="url(#vEgg)" role="img" aria-label="Photo: toddler peeking out of a giant sculpted egg in a garden"/>
    </svg>
    <h2 class="v-title abs" style="top:18px;">
      <span class="name" style="font-size:26px;">Sprout &amp; Shine</span>
      <span class="series" style="font-size:19px;margin-top:3px;">Educational Series<sup>SM</sup></span>
    </h2>
    <ul class="v-list abs" style="top:84px;">
      <li>Non-GMO/Organic Family &amp; Community Gardening Workshops;</li>
      <li>K-12 Common Core/STEM Curricula Development;</li>
      <li>Community Service Projects;</li>
      <li>Online Gardening &amp; Teaching Communities;</li>
      <li>Project-Based Learning Activities;</li>
      <li>Youth Leadership Projects;</li>
      <li>Fun Contests and Prizes;</li>
      <li>Corporate &amp; Small Business Social Responsibility Programs;</li>
      <li>K-12 Staff Development<br>Education Research &amp; Reporting.</li>
    </ul>
  </section>

  <span class="option-label" style="left:26px;top:576px;">2</span>

  <!-- Option 2 front -->
  <section class="card h-card" style="left:71px;top:562px;">
    <div class="h-bar"></div>
    <svg class="art" width="454" height="276" viewBox="0 0 454 276">
      <defs>
        <linearGradient id="hGarden" x1="0" y1="0" x2="0" y2="1">
          <stop offset="0" stop-color="#a99a7c"/>
          <stop offset=".6" stop-color="#7f7a62"/>
          <stop offset="1" stop-color="#d8642a"/>
        </linearGradient>
      </defs>
      <path d="M454 92 Q290 98 244 276" stroke="var(--arc-green)" stroke-width="8" fill="none"/>
      <path d="M454 100 Q298 108 254 276 H454 Z" fill="url(#hGarden)" role="img" aria-label="Photo: young children sitting in a garden behind orange tulips"/>
    </svg>
    <h1 class="h-title abs" style="left:30px;top:38px;">
      <span style="display:block;font-size:35px;">Sprout &amp; Shine</span>
      <span style="display:block;font-size:26px;margin-top:8px;">Educational Series<sup>SM</sup></span>
    </h1>
    <div class="h-contact abs" style="left:34px;top:140px;">
      <p><svg width="18" height="18" viewBox="0 0 24 24" fill="none" stroke="#2f5a14" stroke-width="1.6"><circle cx="12" cy="12" r="9.5"/><ellipse cx="12" cy="12" rx="4.2" ry="9.5"/><path d="M2.5 12h19M4 7h16M4 17h16"/></svg>www.sprout-and-shine.example.org</p>
      <p><svg width="18" height="18" viewBox="0 0 24 24"><path d="M6.6 10.8a15.1 15.1 0 0 0 6.6 6.6l2.2-2.2c.3-.3.7-.4 1-.2 1.1.4 2.3.6 3.6.6.6 0 1 .4 1 1V20c0 .6-.4 1-1 1A17 17 0 0 1 3 4c0-.6.4-1 1-1h3.5c.6 0 1 .4 1 1 0 1.3.2 2.5.6 3.6.1.3 0 .7-.2 1z" fill="#2f5a14"/></svg>(555) 214-7390</p>
    </div>
    <span class="brand-name abs" style="left:34px;top:234px;">Tamarind Valley Families</span>
  </section>

  <!-- Option 2 back -->
  <section class="card h-card" style="left:73px;top:876px;">
    <div class="h-bar"></div>
    <svg class="art" width="454" height="276" viewBox="0 0 454 276">
      <defs>
        <linearGradient id="hVines" x1="0" y1="0" x2="0" y2="1">
          <stop offset="0" stop-color="#6f9a4c"/>
          <stop offset="1" stop-color="#355f22"/>
        </linearGradient>
      </defs>
      <path d="M454 96 Q300 100 248 276" stroke="var(--arc-green)" stroke-width="8" fill="none"/>
      <path d="M454 104 Q308 110 258 276 H454 Z" fill="url(#hVines)" role="img" aria-label="Photo: woman picking peas in a community vegetable garden"/>
    </svg>
    <h2 class="h-title abs" style="left:32px;top:33px;font-size:23px;">Sprout &amp; Shine Educational Series<sup>SM</sup></h2>
    <ul class="h-list abs" style="left:32px;top:77px;">
      <li>Non-GMO/Organic Family &amp; Community Gardening Workshops</li>
      <li>K-12 Common Core/STEM Curricula Development</li>
      <li>Community Service Projects</li>
      <li>Online Gardening &amp; Teaching Communities</li>
      <li>Project-Based Learning Activities</li>
      <li>Youth Leadership Projects</li>
      <li>Fun Contests and Prizes</li>
      <li>Corporate &amp; Small Business Social<br>Responsibility Programs</li>
      <li>K-12 Staff Development</li>
      <li>Education Research &amp; Reporting</li>
    </ul>
  </section>

</main>
</body>
</html>
```